business card for horse saddlery

after a new business card for our saddlery, i will add 2 logos we have previously used and they can be used (or not) . Any images can be used from our website also at www.harrowfields.net.au, I have also added our brand logo, which may be good to incorporate on back ? we have over 15, 000 items online, ship Australia Wide.

Target Market(s)

horse owners

Industry/Entity Type

Retail - Equestrian

Contact Information for Business Card

Harrowfield Horse Supplies, 1300 48 62 90, www.harrowfields.net.au, 27 Lindqvist Rd Marrowbank Q 4587

Requirements
Must have
• trailgem is our brand so trailgem logo on back as 'distributers of', easy to read
Nice to have
• professional but fun
Should not have
• double sided (description wont save double sided)

```html
<!DOCTYPE html>
<html lang="en">
<head>
<meta charset="utf-8">
<title>Harrowfield Horse Supplies – Business Card</title>
<link href="https://fonts.googleapis.com/css2?family=Cormorant+Garamond:wght@500&family=Questrial&display=swap" rel="stylesheet">
<style>
  :root {
    --backdrop: #2b2b2d;
    --card: #ffffff;
    --card-shade: #ececee;
    --ink: #3c3c40;
    --ink-soft: #6a6a70;
    --brand-navy: #1d3f7a;
    --brand-sky: #3a9fd8;
    --brand-blue: #2f6fc4;
    --divider: #9a9ab8;
  }
  * { margin: 0; padding: 0; box-sizing: border-box; }
  html, body {
    width: 1200px; height: 900px; overflow: hidden;
    background: var(--backdrop);
  }
  .canvas {
    position: relative; width: 1200px; height: 900px;
    display: flex; flex-direction: column; align-items: center;
    justify-content: center; gap: 52px;
  }
  .card {
    position: relative; width: 630px; height: 360px;
    background: linear-gradient(120deg, var(--card-shade) 0%, var(--card) 55%);
    box-shadow: 0 18px 40px rgba(0,0,0,0.45);
  }

  /* Front */
  .card-front .brand-block {
    position: absolute; right: 58px; bottom: 78px;
    display: flex; flex-direction: column; align-items: flex-start;
  }
  .brand-mark {
    width: 22px; height: 22px; border-radius: 50%;
    background: var(--brand-navy); margin-bottom: 14px; margin-left: 4px;
  }
  .brand-kicker {
    font-family: "Questrial", sans-serif; font-size: 15px;
    color: var(--ink-soft); letter-spacing: 0.5px; margin-left: 4px;
  }
  .brand-name {
    font-family: "Cormorant Garamond", serif; font-weight: 500;
    font-size: 62px; line-height: 1; letter-spacing: 1px;
    color: var(--brand-navy);
  }

  /* Back */
  .card-back .contact {
    position: absolute; left: 0; top: 0; width: 300px; height: 100%;
    display: flex; flex-direction: column; justify-content: center;
    align-items: flex-end; padding-right: 22px; gap: 6px;
    font-family: "Questrial", sans-serif; color: var(--ink);
  }
  .contact-line {
    display: flex; align-items: center; gap: 8px;
    font-size: 17px; line-height: 1.25; text-align: right;
  }
  .contact-line svg { width: 15px; height: 15px; flex: none; }
  .contact-address { align-items: flex-start; }
  .contact-address span { display: block; }
  .divider {
    position: absolute; left: 320px; top: 80px; width: 1px; height: 200px;
    background: var(--divider);
  }
  .card-back .web-brand {
    position: absolute; left: 321px; right: 0; top: 0; bottom: 0;
    display: flex; align-items: center; justify-content: center; gap: 10px;
  }
  .web-brand-mark {
    width: 18px; height: 18px; border-radius: 50%; background: var(--brand-sky);
  }
  .web-brand-name {
    font-family: "Questrial", sans-serif; font-size: 30px;
    color: var(--brand-blue);
  }
</style>
</head>
<body>
<main class="canvas">
  <section class="card card-front" aria-label="Card front">
    <div class="brand-block">
      <div class="brand-mark"></div>
      <p class="brand-kicker">Distributers Of</p>
      <p class="brand-name">TRAILGEM</p>
    </div>
  </section>

  <section class="card card-back" aria-label="Card back">
    <div class="contact">
      <p class="contact-line">1300 48 62 90
        <svg viewBox="0 0 24 24" aria-hidden="true"><path fill="var(--brand-sky)" d="M6.6 10.8a15 15 0 0 0 6.6 6.6l2.2-2.2c.3-.3.7-.4 1-.2 1.1.4 2.3.6 3.6.6.6 0 1 .4 1 1V20c0 .6-.4 1-1 1A17 17 0 0 1 3 4c0-.6.4-1 1-1h3.5c.6 0 1 .4 1 1 0 1.3.2 2.5.6 3.6.1.3 0 .7-.2 1z"/></svg>
      </p>
      <p class="contact-line">www.harrowfields.net.au
        <svg viewBox="0 0 24 24" aria-hidden="true"><circle cx="12" cy="12" r="9" fill="none" stroke="var(--brand-sky)" stroke-width="2.4"/><path d="M3 12h18M12 3c3 3 3 15 0 18M12 3c-3 3-3 15 0 18" fill="none" stroke="var(--brand-sky)" stroke-width="1.6"/></svg>
      </p>
      <p class="contact-line contact-address"><span>27 Lindqvist Rd.<br>Marrowbank Q 4587</span>
        <svg viewBox="0 0 24 24" aria-hidden="true"><path fill="var(--brand-sky)" d="M12 2a7 7 0 0 0-7 7c0 5 7 13 7 13s7-8 7-13a7 7 0 0 0-7-7zm0 9.5A2.5 2.5 0 1 1 12 6.5a2.5 2.5 0 0 1 0 5z"/></svg>
      </p>
    </div>
    <div class="divider"></div>
    <div class="web-brand">
      <div class="web-brand-mark"></div>
      <p class="web-brand-name">harrowfields.net.au</p>
    </div>
  </section>
</main>
</body>
</html>
```